Law Firm Profile

I need a Law firm Profile design. Something professional, corporate inspired, unique and sophisticated. Preferred colours are blue, grey and white. Completion timeline is 5 days. Details of law firm are in the uploaded document

```html
<!DOCTYPE html>
<html lang="en">
<head>
<meta charset="utf-8">
<title>Halden Advocates Law Firm – Profile Brochure</title>
<link rel="stylesheet" href="https://fonts.googleapis.com/css2?family=Montserrat:wght@300;400;500;600&family=Oswald:wght@500;600&display=swap">
<style>
:root{
  --page:#eeeef0;
  --paper:#ffffff;
  --blue:#1b6fc2;
  --blue-deep:#0f4f9a;
  --blue-light:#2d86d6;
  --heading:#1565b8;
  --grey:#7b7c7f;
  --grey-dark:#5a5b5e;
  --text:#56575a;
  --white:#ffffff;
}
*{box-sizing:border-box;margin:0;padding:0}
html,body{width:1200px;height:2574px;overflow:hidden}
body{background:var(--page);font-family:"Montserrat",sans-serif;font-weight:300;color:var(--text);position:relative}
.spread{position:absolute;left:110px;width:980px;height:692px;display:flex;box-shadow:0 26px 22px -18px rgba(0,0,0,.28)}
.spread--outside{top:985px}
.spread--inside{top:1770px}
.panel{position:relative;width:327px;height:100%;overflow:hidden}
.panel--white{background:var(--paper)}
.panel--blue{background:linear-gradient(180deg,var(--blue) 0%,var(--blue-light) 55%,var(--blue) 100%);color:var(--white)}
.panel--blue-deep{background:linear-gradient(170deg,#1763b3 0%,#1a6cc0 40%,#124f98 100%);color:var(--white)}
.panel--cover{background:linear-gradient(90deg,#ffffff 0%,#f4f4f5 60%,#dedfe1 100%)}
.copy{position:absolute;left:28px;right:28px}
.copy p{font-size:11.2px;line-height:14px;text-align:justify;margin-bottom:10px}
.heading{font-family:"Montserrat",sans-serif;font-weight:500;color:var(--heading);font-size:13.5px;line-height:17px;margin-top:2px}
.panel--blue-deep .heading,.panel--blue-deep h4{color:var(--white)}
.intro-box{position:absolute;left:28px;top:0;width:270px;height:158px;background:var(--grey);color:var(--white);padding:24px 16px 0}
.intro-box p{font-size:11.2px;line-height:14px;text-align:justify}
.photo{position:absolute;left:28px;width:270px}
.photo--handshake{top:502px;height:190px;background:linear-gradient(120deg,#c98a52 0%,#e7c79e 35%,#8c6a4e 70%,#3a2a22 100%)}
.photo--family{top:173px;height:217px;background:radial-gradient(circle at 62% 58%,#f3d79a 0%,#c9925a 35%,#4a3a33 80%,#2c2521 100%)}
.brand-mark{display:flex;align-items:center;gap:10px;justify-content:center}
.brand-mark__dot{width:16px;height:16px;border-radius:50%;background:var(--white)}
.brand-mark__name{font-family:"Montserrat",sans-serif;font-weight:500;font-size:26px;letter-spacing:1px;color:var(--white)}
.panel--blue .brand-mark{position:absolute;top:55px;left:0;right:0}
.centered{position:absolute;left:28px;right:28px;text-align:center}
.centered h3{font-weight:500;font-size:15px;line-height:19px;letter-spacing:.3px}
.centered p{font-size:11.4px;line-height:14px}
.core-values{top:172px}
.core-values p{margin-top:5px;text-align:justify;text-align-last:center}
.address{top:423px}
.address p{font-size:12.5px;line-height:16px;margin-top:6px}
.cell{top:560px}
.cell h3{letter-spacing:2px}
.cell p{font-size:12.5px;line-height:16px;margin-top:2px}
.email{top:640px;font-weight:500;font-size:14px}
.cover-photo{position:absolute;top:0;left:0}
.cover-brand{position:absolute;top:372px;left:0;right:0;display:flex;justify-content:center;align-items:center;gap:10px}
.cover-brand__square{width:18px;height:18px;background:var(--blue)}
.cover-brand__name{font-family:"Montserrat",sans-serif;font-weight:500;font-size:27px;color:var(--blue);letter-spacing:1px}
.cover-title{position:absolute;top:505px;left:0;right:0;text-align:center;font-family:"Oswald",sans-serif;font-weight:600;line-height:44px}
.cover-title__main{display:block;font-size:44px;color:var(--blue);letter-spacing:.5px}
.cover-title__sub{display:block;font-size:44px;color:var(--grey-dark)}
.cover-web{position:absolute;top:643px;left:0;right:0;text-align:center;font-weight:500;font-size:14px;color:var(--grey-dark);letter-spacing:.5px}
.panel--blue-deep .copy p{font-size:11.2px;line-height:14px;margin-bottom:6px}
.personnel{font-weight:500;font-size:13px;line-height:16px}
.staff-list{list-style:none;font-size:11px;line-height:14px;color:var(--grey-dark);text-transform:uppercase}
.staff-list li span{display:inline-block;width:18px;font-weight:500}
.staff-label{font-weight:600;color:var(--heading);font-size:11.5px;margin:4px 0 0}
</style>
</head>
<body>

<!-- Outside spread -->
<section class="spread spread--outside">
  <div class="panel panel--white">
    <div class="intro-box">
      <p>Halden Advocates is an established legal firm situated in Lusaka, Zambia. The firm was founded in 2013 by Mr Robert K Banda S. C, the current Director of Public Prosecutions. The firm represents a wide range of clients both local and international and is dedicated to providing the highest quality of services in various areas of the law including</p>
    </div>
    <div class="copy" style="top:172px">
      <h2 class="heading">Corporate Law</h2>
      <p>We provide comprehensive legal services for corporate clients including in the areas of corporate governance, regulatory compliance, due diligence and risk management advisory. We seamlessly manage the legal aspects of our clients’ transactions and ensure that all documentary and contractual requirements are professionally and strategically executed</p>
      <h2 class="heading">Commercial Law</h2>
      <p>We have vast knowledge and experience in navigating complex commercial legal matters, including contract drafting, negotiations and compliance. We are aligned with the international environment and our lawyers keep up to date on evolving rules of international law and any applicable conflict of laws issues. Our lawyers understand the interplay between the evolving digitalization of the business environment, jurisdictional variances and the legal implications of innovations to the legal environment</p>
    </div>
    <div class="photo photo--handshake" role="img" aria-label="Photo of two business people shaking hands over a desk with a judge's gavel"></div>
  </div>

  <div class="panel panel--blue">
    <div class="brand-mark"><span class="brand-mark__dot"></span><span class="brand-mark__name">Halden</span></div>
    <div class="centered core-values">
      <h3>CORE VALUES</h3>
      <p>We take pride in the quality of our legal services in which we incorporate our core values which include integrity, passion, credibility, continuous professional development and excellent client care in the management of our clients’ instructions. The firm is regulated by the Bar Society of Zambia, and adherence to legal ethics and conduct forms the backbone of our practice and the firm’s culture. We also aim to efficiently to harness creative, bespoke and expert solutions to meet every client’s particular needs.</p>
    </div>
    <div class="centered address">
      <h3>BUSINESS ADDRESS<br>AND CONTACT INFORMATION</h3>
      <p>Plot No. 41, Kafue Crescent,<br>Woodlands Park</p>
      <p>P.O. Box 31207, Ridgeway,<br>Lusaka, Zambia</p>
    </div>
    <div class="centered cell">
      <h3>CELL</h3>
      <p>+260700410112 +260900410134<br>+260970410156 +260760410178</p>
    </div>
    <div class="centered email">haldenadvocates@mail.com</div>
  </div>

  <div class="panel panel--cover">
    <svg class="cover-photo" width="327" height="330" viewBox="0 0 327 330" role="img" aria-label="Photo of a lawyer in a suit writing in a notebook beside a wooden gavel">
      <defs>
        <linearGradient id="coverPhotoTone" x1="0" y1="0" x2="1" y2="1">
          <stop offset="0" stop-color="#b9b6b0"/>
          <stop offset=".45" stop-color="#4a4644"/>
          <stop offset=".75" stop-color="#2a2523"/>
          <stop offset="1" stop-color="#6b5140"/>
        </linearGradient>
      </defs>
      <polygon points="0,0 327,0 327,325 0,262" fill="url(#coverPhotoTone)"/>
    </svg>
    <div class="cover-brand"><span class="cover-brand__square"></span><span class="cover-brand__name">Halden</span></div>
    <h1 class="cover-title"><span class="cover-title__main">HALDEN ADVOCATES</span><span class="cover-title__sub">LAW FIRM</span></h1>
    <div class="cover-web">www.haldenlawfirm.net</div>
  </div>
</section>

<!-- Inside spread -->
<section class="spread spread--inside">
  <div class="panel panel--white">
    <div class="copy" style="top:36px">
      <h2 class="heading">Estate and Family Law</h2>
      <p>We are well versed in handling estate planning, Wills, Trusts, guardianship, divorce and probate matters to address clients’ specific legal needs. Our flexible approach in implementing the full range of established dispute resolution methods at appropriate stages of the transactions and matters speaks to the successful management of even the most complex cases</p>
    </div>
    <div class="photo photo--family" role="img" aria-label="Silhouette photo of a family holding up a paper house at sunset"></div>
    <div class="copy" style="top:398px">
      <h2 class="heading">Debt Collection</h2>
      <p>We efficiently handle the recovery process which is crucial for the businesses, financial institutions and individuals we represent, ensuring that disruptions and cost to our clients are mitigated</p>
      <h2 class="heading">Civil and Criminal Litigation</h2>
      <p>We have a notable and well respected track record in the area of litigation and all ancillary processes, we have handled major cases in commercial, criminal, constitutional and other areas of the law. We are committed to ensuring that our work is backed by meticulous legal analysis, structure and sound strategy, ensuring that we draw from the benefits of the integrated and multi-faceted nature of our practice to ensure best results for our clients</p>
    </div>
  </div>

  <div class="panel panel--blue-deep" role="img" aria-label="Blue panel with a faint photo of a statue of justice">
    <div class="copy" style="top:36px">
      <h2 class="heading">Administrative Law</h2>
      <p>We represent a significant number of clients in the area of public law and have handled a large number of judicial review matters regarding immigration and deportation matters, regulatory infringements among others. We are committed to offering comprehensive guidance, clear communication and swift and appropriate response and high quality strategy from the administrative stage, at first instance, and across all stages of the appeal process</p>
      <h2 class="heading">Land Law</h2>
      <p>We have handled a wide range of land matters including trespass litigation, encroachment, rectifications and conveyancing and manage a substantial caseload of cases</p>
      <h2 class="heading">Constitutional Law</h2>
      <p>We are a leading firm in constitutional law matters and have handled a plethora of presidential, parliamentary and local government election petitions. Our vast expertise in constitutional law is also displayed by our extensive portfolio in handling all manner of novel challenging matters in this area from constitutional interpretation to general constitutional petitions as well as motions. We have a strong database of case-law records and material which enhances our nuanced and detailed understanding of constitutional law enabling us to render well researched legal opinions to our clients</p>
      <h2 class="personnel">KEY PERSONNEL<br>MANAGING PARTNER<br>Naomi Chanda</h2>
      <p>Naomi Chanda has more than seven years of experience in various areas of the law including commercial law, mining law, construction law, labour law, company law, constitutional law, human rights law, ICT law, administrative law, legislative drafting, civil and criminal litigation and energy law</p>
    </div>
  </div>

  <div class="panel panel--white">
    <div class="copy" style="top:36px">
      <p>studied law at the Kafue Valley University, graduated in 2015 and was admitted to the bar in 2016. Since April 2022 She has sat on the licensing committee of the Power Sector Licensing Board and is well versed in the matters relating to the energy sector. She is a member of the Open Media Trust and advocates for digital rights and freedom of expression. She provides legal advisory services to various civil society organizations and undertakes strategic litigation and she holds a postgraduate diploma in legislative drafting and advocates for legislative reform and advancement in various areas of the law</p>
      <h2 class="heading">ASSOCIATE – Grace Mulenga</h2>
      <p>Grace Mulenga has over three years of experience in civil litigation, conveyancing, handling corporate and commercial transactions, contract drafting, family law, human rights law, labour disputes, debt recovery as well as administrative law. She studied at Northern Open University and graduated in 2016 and was admitted to the Bar in 2020. She is a member of the Public Interest Committee of the Bar Society of Zambia and has a keen interest in human rights matters</p>
      <h2 class="heading">Management Structure</h2>
      <p>We have a dedicated team of personnel whose primary goal is to provide the highest quality of service in compliance with all applicable rules of professional conduct. Our support team is friendly, skilled and diverse and work together to ensure that the lawyer-client relationship is seamlessly and properly managed</p>
      <ul class="staff-list" style="margin-top:24px">
        <li><span>1.</span>Managing Partner</li>
        <li><span>2.</span>Partner (S)</li>
        <li><span>3.</span>Associate (S)</li>
      </ul>
      <p class="staff-label">SUPPORT STAFF:</p>
      <ul class="staff-list">
        <li><span>4.</span>Office Manager</li>
        <li><span>5.</span>Assistant Office Manager</li>
        <li><span>6.</span>Legal Clerk</li>
        <li><span>7.</span>Receptionist</li>
      </ul>
    </div>
  </div>
</section>

</body>
</html>
```